Professional and creative business card design for recruiting service providers

Our company supports German medium-sized companies in filling vacancies promptly. For this we use social media marketing and bring our customers into the visibility.

We want a professional but also creative design for our business cards.

Please look at lindqvar-staff.de to get an impression of our CI.

Target Market(s)

Small and medium-sized companies in Germany from the industry

Industry/Entity Type

Industrie, Handwerk

Contact Information for Business Card

Name, Position, Telefonnummer, Email, Website

Colors
EE7325
F08F49
F5BC92
FAE3D3
FDF4ED

Requirements
Must have
• A picture of the employee and in the style of www.lindqvar-staff.de

```html
<!DOCTYPE html>
<html lang="de">
<head>
<meta charset="utf-8">
<title>Lindqvar &amp; Staff – Visitenkarte</title>
<link rel="stylesheet" href="https://fonts.googleapis.com/css2?family=Montserrat:wght@500;800&family=Arimo:wght@400&display=swap">
<style>
  :root {
    --orange: #EE7325;
    --orange-soft: #F08F49;
    --ink: #111111;
    --card-black: #070707;
    --brand-dim: #3a3a3a;
    --paper: #ffffff;
    --stage: #2b2b2b;
    --photo-light: #e2e0e3;
    --photo-dark: #2a2c38;
  }
  * { box-sizing: border-box; margin: 0; padding: 0; }
  html, body { width: 1200px; height: 1015px; overflow: hidden; }
  body { background: var(--stage); position: relative; font-family: "Arimo", Arial, sans-serif; }

  .card {
    position: absolute;
    width: 700px;
    height: 400px;
    left: 250px;
    overflow: hidden;
    box-shadow: 0 14px 30px rgba(0,0,0,.45);
  }
  .card__stripe {
    position: absolute;
    left: 0; right: 0; bottom: 0;
    height: 12px;
    background: var(--orange);
  }

  /* back side */
  .card--back { top: 70px; background: var(--card-black); }
  .card--back .brand {
    position: absolute;
    left: 50%; top: 50%;
    transform: translate(-50%, -56%);
    display: flex; align-items: center; gap: 20px;
  }
  .card--back .brand__mark { background: var(--brand-dim); }
  .card--back .brand__name { color: var(--brand-dim); font-size: 38px; }

  /* front side */
  .card--front { top: 540px; background: var(--paper); }

  .brand { display: flex; align-items: center; gap: 16px; }
  .brand__mark { width: 46px; height: 46px; background: var(--orange); flex: none; }
  .brand__name {
    font-family: "Montserrat", Arial, sans-serif;
    font-weight: 800;
    letter-spacing: 2px;
    line-height: 1.05;
    text-transform: uppercase;
  }
  .card--front .brand { position: absolute; left: 56px; top: 110px; }
  .card--front .brand__name { color: var(--ink); font-size: 30px; }

  .contact {
    position: absolute;
    left: 62px; top: 262px;
    list-style: none;
    font-size: 18px;
    color: var(--ink);
  }
  .contact li { display: flex; align-items: center; gap: 10px; height: 27px; }
  .contact svg { width: 18px; height: 18px; flex: none; }

  .portrait {
    position: absolute;
    left: 412px; top: 36px;
    width: 256px; height: 212px;
    border: 2px solid var(--orange);
    background: linear-gradient(180deg, var(--photo-light) 0%, var(--photo-light) 45%, var(--photo-dark) 100%);
  }

  .person {
    position: absolute;
    right: 32px; top: 262px;
    text-align: right;
  }
  .person__name {
    font-family: "Montserrat", Arial, sans-serif;
    font-weight: 800;
    font-size: 22px;
    letter-spacing: 1px;
    color: var(--ink);
  }
  .person__role {
    font-size: 14px;
    letter-spacing: 1px;
    color: var(--ink);
    margin-top: 2px;
  }
</style>
</head>
<body>

  <section class="card card--back" aria-label="Kartenrückseite">
    <div class="brand">
      <span class="brand__mark"></span>
      <p class="brand__name">Lindqvar<br>&amp; Staff</p>
    </div>
    <div class="card__stripe"></div>
  </section>

  <section class="card card--front" aria-label="Kartenvorderseite">
    <div class="brand">
      <span class="brand__mark"></span>
      <p class="brand__name">Lindqvar<br>&amp; Staff</p>
    </div>

    <ul class="contact">
      <li>
        <svg viewBox="0 0 24 24" fill="var(--orange)" aria-hidden="true"><path d="M6.6 10.8a15.1 15.1 0 0 0 6.6 6.6l2.2-2.2a1 1 0 0 1 1-.25 11.4 11.4 0 0 0 3.6.57 1 1 0 0 1 1 1V20a1 1 0 0 1-1 1A17 17 0 0 1 3 4a1 1 0 0 1 1-1h3.5a1 1 0 0 1 1 1c0 1.25.2 2.45.57 3.57a1 1 0 0 1-.25 1z"/></svg>
        044-987 654 321
      </li>
      <li>
        <svg viewBox="0 0 24 24" fill="var(--orange)" aria-hidden="true"><path d="M2 5h20v14H2z"/><path d="M2 5l10 8 10-8" fill="none" stroke="#fff" stroke-width="1.6"/></svg>
        info@lindqvar-staff.de
      </li>
      <li>
        <svg viewBox="0 0 24 24" fill="none" stroke="var(--orange)" stroke-width="2" aria-hidden="true"><circle cx="12" cy="12" r="9.5"/><ellipse cx="12" cy="12" rx="4" ry="9.5"/><path d="M2.5 12h19M4 7h16M4 17h16"/></svg>
        www.lindqvar-staff.de
      </li>
    </ul>

    <div class="portrait" role="img" aria-label="Porträtfoto des Geschäftsführers vor hellgrauem Hintergrund"></div>

    <div class="person">
      <p class="person__name">MARKUS FELDNER</p>
      <p class="person__role">MANAGING DIRECTOR</p>
    </div>

    <div class="card__stripe"></div>
  </section>

</body>
</html>
```